Brellwick Partners, LLC Stationary

Brellwick Partners, LLC is a new financial planning and consulting company. We are looking for designs on business cards, letterhead, envelopes, and anything else that would be useful. Our preference for business card design is two sided. We are looking for a professional and clean look with incorporating the logo and patriotic feel. Thank you to all who participate and good luck!

```html
<!DOCTYPE html>
<html lang="en">
<head>
<meta charset="utf-8">
<title>Brellwick Partners, LLC – Business Card</title>
<link rel="stylesheet" href="https://fonts.googleapis.com/css2?family=Montserrat:wght@600;700&family=Open+Sans:wght@300;400&display=swap">
<style>
  :root {
    --navy: #123f6d;
    --navy-dark: #0b2c4f;
    --red: #c8303a;
    --ink: #6b6f74;
    --paper: #ffffff;
    --stage: #e9e7e3;
  }
  * { margin: 0; padding: 0; box-sizing: border-box; }
  html, body { width: 1200px; height: 950px; overflow: hidden; background: var(--stage); }
  .sheet { position: relative; width: 1200px; height: 950px; }

  .card {
    position: absolute; left: 250px; width: 700px; height: 400px;
    box-shadow: 0 6px 18px rgba(0,0,0,.18); overflow: hidden;
  }
  .card-front { top: 55px; background: var(--paper); }
  .card-back { top: 495px; background: var(--navy); }

  /* Front: brand block */
  .brand { position: absolute; left: 58px; top: 128px; display: flex; align-items: center; gap: 14px; }
  .brand-dot { width: 34px; height: 34px; border-radius: 50%; background: var(--navy); }
  .brand-name {
    font-family: "Montserrat", sans-serif; font-weight: 700; font-size: 27px;
    color: var(--navy); letter-spacing: .5px; text-transform: uppercase;
  }
  .brand-tagline {
    position: absolute; left: 106px; top: 172px;
    font-family: "Open Sans", sans-serif; font-size: 10px; letter-spacing: 1.6px;
    color: var(--red); text-transform: uppercase;
  }

  /* Front: name ribbon */
  .ribbon { position: absolute; right: 0; top: 44px; width: 300px; height: 82px; }
  .ribbon-text { position: absolute; right: 30px; top: 56px; text-align: left; color: #fff; width: 230px; }
  .person-name { font-family: "Montserrat", sans-serif; font-weight: 600; font-size: 22px; letter-spacing: 1px; }
  .person-role { font-family: "Open Sans", sans-serif; font-weight: 300; font-size: 17px; letter-spacing: 1px; margin-top: 2px; }

  /* Front: contact */
  .contact {
    position: absolute; left: 106px; top: 232px; list-style: none;
    font-family: "Open Sans", sans-serif; font-weight: 300; font-size: 16px;
    color: var(--ink); line-height: 25px;
  }
  .contact li { display: flex; align-items: center; gap: 9px; }
  .contact .address { padding-left: 0; }
  .contact svg { width: 13px; height: 13px; fill: var(--navy); flex: none; }

  /* Back */
  .back-mark {
    position: absolute; left: 50%; top: 50%; transform: translate(-50%, -50%);
    display: flex; align-items: center; gap: 14px;
  }
  .back-dot { width: 40px; height: 40px; border-radius: 50%; background: #fff; }
  .back-name {
    font-family: "Montserrat", sans-serif; font-weight: 700; font-size: 30px;
    color: #fff; letter-spacing: .5px; text-transform: uppercase;
  }
  .back-web {
    position: absolute; left: 40px; bottom: 32px;
    font-family: "Open Sans", sans-serif; font-size: 15px; letter-spacing: 1.5px; color: #fff;
  }
</style>
</head>
<body>
<main class="sheet">
  <section class="card card-front" aria-label="Business card front">
    <div class="brand">
      <span class="brand-dot"></span>
      <span class="brand-name">Brellwick Partners, LLC</span>
    </div>
    <p class="brand-tagline">Financial Planning and Consulting</p>

    <svg class="ribbon" viewBox="0 0 300 82" aria-hidden="true">
      <polygon points="0,62 34,62 22,72 34,82 0,82" fill="var(--navy-dark)"/>
      <polygon points="18,0 300,0 300,62 18,62" fill="var(--navy)"/>
      <polygon points="18,62 34,62 34,74" fill="#071d35"/>
    </svg>
    <div class="ribbon-text" style="top:46px;">
      <div class="person-name">DANIEL MERCER</div>
      <div class="person-role">CEO/FOUNDER</div>
    </div>

    <ul class="contact">
      <li class="address">4120 Larkspur Court</li>
      <li class="address">Juneau, Alaska 99801</li>
      <li><svg viewBox="0 0 24 24"><path d="M6.6 10.8a15 15 0 0 0 6.6 6.6l2.2-2.2c.3-.3.7-.4 1-.2 1.1.4 2.3.6 3.6.6.6 0 1 .4 1 1V20c0 .6-.4 1-1 1A17 17 0 0 1 3 4c0-.6.4-1 1-1h3.5c.6 0 1 .4 1 1 0 1.3.2 2.5.6 3.6.1.3 0 .7-.2 1z"/></svg>555 214 7730</li>
      <li><svg viewBox="0 0 24 24"><path d="M7 1h10a2 2 0 0 1 2 2v18a2 2 0 0 1-2 2H7a2 2 0 0 1-2-2V3a2 2 0 0 1 2-2zm0 3v14h10V4z"/></svg>555 381 6042</li>
      <li><svg viewBox="0 0 24 24"><path d="M2 5h20v14H2zm2 2v.5l8 5 8-5V7l-8 5z"/></svg>hello@brellwick.com</li>
      <li><svg viewBox="0 0 24 24"><path d="M12 2a10 10 0 1 0 0 20 10 10 0 0 0 0-20zm0 2c.9 1.2 1.6 2.7 2 4h-4c.4-1.3 1.1-2.8 2-4zM4.3 14a8 8 0 0 1 0-4h3.4a16 16 0 0 0 0 4zm5.4 0a14 14 0 0 1 0-4h4.6a14 14 0 0 1 0 4zm6.6 0a16 16 0 0 0 0-4h3.4a8 8 0 0 1 0 4zM12 20c-.9-1.2-1.6-2.7-2-4h4c-.4 1.3-1.1 2.8-2 4z"/></svg>www.brellwick.com</li>
    </ul>
  </section>

  <section class="card card-back" aria-label="Business card back">
    <div class="back-mark">
      <span class="back-dot"></span>
      <span class="back-name">Brellwick Partners, LLC</span>
    </div>
    <p class="back-web">www.brellwick.com</p>
  </section>
</main>
</body>
</html>
```